MRT Property - Business Cards

Looking for a business card & general letterhead, signage etc design for our new logo.

Colours:
000a20
0056a2
00b5ef
0088ce
68cef2

Fonts:
Poppins
Karla

Please keep look and feel of new brand - example in the zip package I sent.

```html
<!DOCTYPE html>
<html lang="en">
<head>
<meta charset="utf-8">
<title>MRT Property – Stationery</title>
<link href="https://fonts.googleapis.com/css2?family=Karla:wght@400;500&family=Poppins:wght@500;600&display=swap" rel="stylesheet">
<style>
  :root{
    --ink:#000a20;
    --navy:#1b2240;
    --blue:#0056a2;
    --sky:#00b5ef;
    --mid:#0088ce;
    --light:#68cef2;
    --paper:#ffffff;
    --text:#555b66;
    --stage:#e9ebef;
  }
  *{box-sizing:border-box;margin:0;padding:0}
  html,body{width:1200px;height:800px;overflow:hidden}
  body{background:var(--stage);font-family:"Karla",sans-serif;color:var(--text);position:relative}

  .brand-name{font-family:"Poppins",sans-serif;font-weight:600;color:var(--blue);letter-spacing:.5px;display:flex;align-items:center;gap:8px;white-space:nowrap}
  .brand-dot{width:12px;height:12px;border-radius:50%;background:var(--blue);flex:none}

  .card{position:absolute;left:90px;width:350px;height:200px;box-shadow:0 6px 16px rgba(0,10,32,.18);overflow:hidden}
  .card-front{top:130px;background:var(--navy);display:flex;align-items:center;justify-content:center}
  .card-front .brand-name{font-size:30px;color:var(--mid)}
  .card-front .brand-dot{width:18px;height:18px;background:var(--mid)}

  .card-back{top:390px;background:var(--paper)}
  .card-back .brand-name{position:absolute;right:28px;top:26px;font-size:19px}
  .holder{position:absolute;left:28px;top:100px;right:28px;border-bottom:1px solid var(--light);padding-bottom:3px}
  .holder-name{font-family:"Poppins",sans-serif;font-weight:600;font-size:11px;color:var(--blue);letter-spacing:.3px}
  .holder-role{font-size:9px;color:var(--light)}
  .card-contact{position:absolute;left:28px;top:140px;font-size:9px;line-height:12px;color:var(--text)}
  .card-address{position:absolute;right:28px;top:140px;font-size:9px;line-height:12px;text-align:right}
  .card-address .firm{color:var(--mid)}
  .contact-row{display:flex;align-items:center;gap:5px}
  .contact-row svg{width:8px;height:8px;flex:none}
  .band{position:absolute;left:0;bottom:0;width:100%;height:8px}

  .letterhead{position:absolute;left:600px;top:30px;width:520px;height:740px;background:var(--paper);box-shadow:0 8px 22px rgba(0,10,32,.18);overflow:hidden}
  .letterhead .brand-name{position:absolute;left:50px;top:62px;font-size:30px}
  .letterhead .brand-dot{width:18px;height:18px}
  .lh-contact{position:absolute;right:50px;top:52px;font-size:9.5px;line-height:12px;width:118px}
  .lh-contact .addr{margin-bottom:6px}
  .lh-contact .contact-row svg{fill:var(--blue)}
  .letter{position:absolute;left:50px;right:50px;top:172px;font-size:9.2px;line-height:14px;text-align:justify}
  .letter p{margin-bottom:13px}
  .signature{width:64px;height:56px;background:linear-gradient(135deg,#eef1f7,#dde3ef);border-radius:4px;margin-top:4px}
</style>
</head>
<body>

  <section class="card card-front" aria-label="Business card front">
    <div class="brand-name"><span class="brand-dot"></span>MRT Property</div>
  </section>

  <section class="card card-back" aria-label="Business card back">
    <div class="brand-name"><span class="brand-dot"></span>MRT Property</div>
    <div class="holder">
      <div class="holder-name">DALEN ORTVIK</div>
      <div class="holder-role">Managing Director</div>
    </div>
    <div class="card-contact">
      <div class="contact-row"><svg viewBox="0 0 10 10" fill="#0056a2"><path d="M2 1h2l1 2-1 1a6 6 0 0 0 2 2l1-1 2 1v2c0 1-1 1-1 1A8 8 0 0 1 1 2s0-1 1-1z"/></svg>(555) 204-7731</div>
      <div class="contact-row"><svg viewBox="0 0 10 10" fill="#0056a2"><path d="M0 2h10v6H0z M0 2l5 3 5-3" stroke="#fff" stroke-width=".8"/></svg>info@mrtproperty.com</div>
      <div class="contact-row"><svg viewBox="0 0 10 10"><circle cx="5" cy="5" r="4.5" fill="#0056a2"/></svg>www.mrtproperty.com</div>
    </div>
    <div class="card-address">
      <div class="firm">MRT Property</div>
      <div>218 W Harlow Ave</div>
      <div>Brookdale, CA 90412</div>
    </div>
    <svg class="band" viewBox="0 0 350 8" preserveAspectRatio="none"><rect width="350" height="8" fill="#68cef2"/><polygon points="0,0 232,0 226,8 0,8" fill="#0056a2"/></svg>
  </section>

  <article class="letterhead" aria-label="Letterhead">
    <div class="brand-name"><span class="brand-dot"></span>MRT Property</div>
    <div class="lh-contact">
      <div class="addr">218 W Harlow Ave<br>Brookdale, CA 90412</div>
      <div class="contact-row"><svg viewBox="0 0 10 10"><path d="M2 1h2l1 2-1 1a6 6 0 0 0 2 2l1-1 2 1v2c0 1-1 1-1 1A8 8 0 0 1 1 2s0-1 1-1z"/></svg>(555) 204-7731</div>
      <div class="contact-row"><svg viewBox="0 0 10 10"><path d="M0 2h10v6H0z M0 2l5 3 5-3" stroke="#fff" stroke-width=".8"/></svg>info@mrtproperty.com</div>
      <div class="contact-row"><svg viewBox="0 0 10 10"><circle cx="5" cy="5" r="4.5"/></svg>www.mrtproperty.com</div>
    </div>
    <div class="letter">
      <p>Dear customer,</p>
      <p>Lorem ipsum dolor sit amet, consectetur adipisicing elit, sed do eiusmod tempor incididunt ut labore et dolore magna aliqua. Ut enim ad minim veniam, quis nostrud exercitation ullamco laboris nisi ut aliquip ex ea commodo consequat. Duis aute irure dolor in reprehenderit in voluptate velit esse cillum dolore eu fugiat nulla pariatur. Excepteur sint occaecat cupidatat non proident, sunt in culpa qui officia deserunt mollit anim id est laborum.</p>
      <p>Lorem ipsum dolor sit amet, consectetur adipisicing elit, sed do eiusmod tempor incididunt ut labore et dolore magna aliqua. Ut enim ad minim veniam, quis nostrud exercitation ullamco laboris nisi ut aliquip ex ea commodo consequat. Duis aute irure dolor in reprehenderit in voluptate velit esse cillum dolore eu fugiat nulla pariatur. Excepteur sint occaecat cupidatat non proident, sunt in culpa qui officia deserunt mollit anim id est laborum.</p>
      <p>Lorem ipsum dolor sit amet, consectetur adipisicing elit, sed do eiusmod tempor incididunt ut labore et dolore magna aliqua. Ut enim ad minim veniam, quis nostrud exercitation ullamco laboris nisi ut aliquip ex ea commodo consequat. Duis aute irure dolor in reprehenderit in voluptate velit esse cillum dolore eu fugiat nulla pariatur. Excepteur sint occaecat cupidatat non proident, sunt in culpa qui officia deserunt mollit anim id est laborum.</p>
      <p>Lorem ipsum dolor sit amet, consectetur adipisicing elit, sed do eiusmod tempor incididunt ut labore et dolore magna aliqua. Ut enim ad minim veniam, quis nostrud exercitation ullamco laboris nisi ut aliquip ex ea commodo consequat. Duis aute irure dolor in reprehenderit.</p>
      <p>Yours Sincerely,</p>
      <div class="signature" role="img" aria-label="Handwritten signature"></div>
    </div>
    <svg class="band" viewBox="0 0 520 12" preserveAspectRatio="none" style="height:12px"><rect width="520" height="12" fill="#68cef2"/><polygon points="0,0 400,0 392,12 0,12" fill="#0056a2"/></svg>
  </article>

</body>
</html>
```